Jewelers Website

This is for the DESIGN ONLY.
I am a software programmer and will be doing the development.
New website design for
www.lunacrestgems.com.au
Need a fresh new look for an online only jewellery business who produce their jewellery by hand. I would like it designed in a parallax style. Feel free to recommend fonts to use for the site. This is an Australian based company located in NSW so shots of sites in NSW might make nice background images.
http://vornaplex.me/demo/#theme=parallax
To contain the below sections
About Us
Contact Us
Gallery
Testimonials
Diamond Types
The colour scheme is to be Black / White and Silver.
With the Parallax style there will be moving sections and images for added impact.
Target Market(s)
Young Adults mainly engagement jewellery

```html
<!DOCTYPE html>
<html lang="en">
<head>
<meta charset="utf-8">
<title>Lunacrest Gems</title>
<link href="https://fonts.googleapis.com/css2?family=Cinzel:wght@400&family=Raleway:wght@300;400;500;600&family=Open+Sans:wght@400;600&display=swap" rel="stylesheet">
<style>
:root{
  --black:#111111;
  --ink:#222222;
  --grey-text:#777777;
  --light-text:#bbbbbb;
  --silver:#c9c9c9;
  --line:#e2e2e2;
  --panel:#f1f1f1;
  --white:#ffffff;
  --dark-band:#1b1b1b;
}
*{margin:0;padding:0;box-sizing:border-box}
html,body{width:1200px;height:4724px;overflow:hidden}
body{position:relative;background:var(--white);font-family:'Raleway',sans-serif;color:var(--ink)}
section,header,nav,footer{position:absolute;left:0;width:1200px}
.abs{position:absolute}
.center{text-align:center;left:0;width:1200px}

/* Hero */
.hero{top:0;height:857px;background:linear-gradient(90deg,#1c1c1c 0%,#3a3a3a 40%,#6b6460 70%,#4a4340 100%)}
.hero-photo{position:absolute;inset:0}
.hero-logo{top:225px;left:465px;width:265px;height:110px;background:#161616;border:2px solid #d9d9d9;color:var(--white);font-weight:500;font-size:30px;letter-spacing:2px;text-align:center;line-height:34px;padding-top:18px}
.hero-title{top:390px;font-family:'Cinzel',serif;font-weight:400;font-size:37px;letter-spacing:2px;color:var(--white)}
.hero-sub{top:470px;font-size:13px;font-weight:500;letter-spacing:.3px;color:var(--white)}
.btn-light{top:541px;left:482px;width:236px;height:46px;border-radius:23px;background:var(--white);color:var(--ink);font-size:13px;font-weight:600;line-height:46px;text-align:center;letter-spacing:.5px}
.dots{top:742px;left:560px;display:flex;gap:16px}
.dots span{width:14px;height:14px;border-radius:50%;background:var(--white)}
.dots span.on{background:transparent;border:3px solid var(--white)}

/* Nav */
.nav{top:857px;height:88px;background:var(--white);border-bottom:1px solid var(--line)}
.nav-logo{top:15px;left:110px;width:146px;height:60px;background:#161616;color:var(--white);font-weight:500;font-size:17px;letter-spacing:1px;text-align:center;line-height:22px;padding-top:8px}
.nav-links{top:37px;left:320px;display:flex;gap:42px;font-size:11px;font-weight:500;color:#444}
.nav-links .active{position:relative;color:var(--black);font-weight:600}
.nav-links .active::after{content:'• • •';position:absolute;left:9px;top:14px;font-size:9px;letter-spacing:1px}
.socials{top:32px;left:975px;display:flex;gap:8px}
.socials span{width:22px;height:22px;border-radius:50%;background:var(--silver)}

/* About */
.about{top:945px;height:504px}
.about-photo{top:55px;left:110px;width:490px;height:386px;background:radial-gradient(ellipse at 50% 55%,#cfd3d8 0%,#9ea3aa 45%,#f4f4f4 80%)}
.about-title{top:60px;left:655px;font-weight:400;font-size:46px;line-height:56px;color:var(--black)}
.about-copy{top:195px;left:655px;width:440px;font-family:'Open Sans',sans-serif;font-size:13px;line-height:20px;color:var(--grey-text)}
.btn-outline{top:412px;left:655px;width:134px;height:44px;border:1px solid #333;font-size:14px;line-height:42px;text-align:center;color:var(--ink)}

/* Features */
.features{top:1449px;height:268px;background:radial-gradient(circle at 20% 30%,#333 0%,#151515 60%),var(--dark-band)}
.features-title{top:30px;font-size:22px;font-weight:500;color:var(--white)}
.feature{top:95px;width:230px;color:var(--white)}
.feature svg{display:block;margin-bottom:12px}
.feature h3{font-size:14px;font-weight:600;margin-bottom:6px}
.feature p{font-family:'Open Sans',sans-serif;font-size:11px;line-height:15px;color:var(--light-text)}

/* Section headings */
.sec-title{font-weight:400;font-size:44px;color:var(--black)}
.sec-sub{font-size:10px;font-weight:600;letter-spacing:.3px;color:var(--ink)}

/* Gallery */
.gallery{top:1717px;height:866px}
.gallery .sec-title{top:50px}
.gallery .sec-sub{top:130px}
.grid{top:183px;left:110px;width:980px;display:grid;grid-template-columns:repeat(4,1fr);grid-template-rows:repeat(3,207px);gap:10px}
.tile{background:linear-gradient(135deg,#d8c3b3,#8a6f62)}
.tile.t2{background:linear-gradient(135deg,#a32a2a,#e6d8d0)}
.tile.t3{background:linear-gradient(135deg,#b88a6c,#efe3d8)}
.tile.t4{background:linear-gradient(135deg,#f4ece6,#c9a58e)}
.tile.t5{background:linear-gradient(135deg,#5a3a2e,#d9b29a)}
.tile.t6{background:linear-gradient(135deg,#f2efe9,#c3a27c)}
.tile.t7{background:linear-gradient(135deg,#f4f4f4,#a9a9a9)}
.tile.t8{background:linear-gradient(135deg,#e0c2ac,#7d5a47)}
.tile.t9{background:linear-gradient(135deg,#8c6a4f,#e8cdb6)}
.tile.t10{background:linear-gradient(135deg,#e6c8b2,#a88068)}
.tile.t11{background:linear-gradient(135deg,#fafafa,#d4c3bb)}
.tile.t12{background:linear-gradient(135deg,#2a1e1a,#9c7460)}

/* Testimonials */
.testimonials{top:2583px;height:410px;background:repeating-linear-gradient(90deg,#2e2e2e 0 60px,#262626 60px 120px)}
.testimonials .sec-title{top:60px;color:var(--white)}
.testimonials .sec-sub{top:135px;color:var(--white)}
.avatar{top:205px;width:114px;height:114px;border-radius:50%;background:linear-gradient(135deg,#e6d2c4,#8c7060);border:4px solid var(--white)}
.quote{top:205px;width:315px;height:142px;background:#4a4a4a;color:var(--light-text);text-align:center;font-family:'Open Sans',sans-serif;font-size:13px;line-height:19px;padding:26px 30px 0}
.quote::before{content:'';position:absolute;left:-14px;top:48px;border:14px solid transparent;border-left:0;border-right-color:#4a4a4a}
.quote cite{display:block;text-align:right;font-style:normal;font-size:12px;margin-top:16px}

/* Diamond types */
.types{top:2993px;height:708px}
.types .sec-title{top:70px}
.types .sec-sub{top:150px}
.gem{width:200px;text-align:center;font-family:'Open Sans',sans-serif;font-size:14px;color:var(--ink)}
.gem .stone{width:100px;height:104px;margin:0 auto 30px;border-radius:22px}
.stone.yellow{background:radial-gradient(circle,#f2dc6a,#8a6d0e)}
.stone.white{background:radial-gradient(circle,#dfe6f2,#5e6a86)}
.stone.black{background:radial-gradient(circle,#4a4a4a,#050505)}
.stone.green{background:radial-gradient(circle,#5ee07a,#0b6d2a)}

/* Contact */
.contact{top:3701px;height:489px;background:var(--panel)}
.contact .sec-title{top:45px}
.contact .sec-sub{top:112px}
.field{left:110px;width:479px;height:45px;background:var(--panel);border:1px solid #dedede;font-size:12px;color:#aaa;padding:12px 14px}
.field.msg{left:617px;width:473px;height:170px}
.btn-dark{top:391px;left:510px;width:183px;height:41px;background:#3a3a3a;color:#ddd;font-size:12px;text-align:center;line-height:41px}

/* Map */
.map{top:4190px;height:447px;background:linear-gradient(135deg,#e8e8e6,#d6d6d3)}
.to-top{top:4597px;left:577px;width:40px;height:40px;background:#111;color:var(--white)}

/* Footer */
.footer{top:4637px;height:87px;background:var(--black);color:var(--light-text);font-size:12px;text-align:center;line-height:87px}
</style>
</head>
<body>

<header class="hero">
  <div class="hero-photo" role="img" aria-label="Model wearing a statement diamond necklace and drop earrings"></div>
  <div class="abs hero-logo">LUNACREST<br>GEMS</div>
  <h1 class="abs center hero-title">FIND THE LIMITLESS CREATIVITY FROM US</h1>
  <p class="abs center hero-sub">LOREM IPSUM DOLOR SIT AMET CONSECTETUER ADIPISCING ELIT SED DIAM NONUMMY</p>
  <div class="abs btn-light">DISCOVER THE COLLECTION</div>
  <div class="abs dots"><span></span><span class="on"></span><span></span><span></span></div>
</header>

<nav class="nav">
  <div class="abs nav-logo">LUNACREST<br>GEMS</div>
  <div class="abs nav-links">
    <span>HOME</span><span class="active">ABOUT US</span><span>GALLERY</span><span>TESTIMONIALS</span><span>DIAMOND TYPES</span><span>CONTACT US</span>
  </div>
  <div class="abs socials"><span></span><span></span><span></span><span></span></div>
</nav>

<section class="about">
  <div class="abs about-photo" role="img" aria-label="Loose brilliant-cut diamonds scattered on white"></div>
  <h2 class="abs about-title">We are the top level<br>Jewellers</h2>
  <p class="abs about-copy">Lorem ipsum dolor sit amet, consectetuer adipiscing elit, sed diam nonummy nibh euismod tincidunt ut laoreet dolore magna aliquam erat volutpat. Ut wisi enim ad minim veniam, quis nostrud exerci tation ullamcorper suscipit lobortis nisl ut aliquip ex ea commodo consequat. Duis autem vel eum iriure dolor in hendrerit in vulputate velit esse molestie consequat, vel illum dolore eu feugiat nulla facilisis at vero eros et accumsan.</p>
  <div class="abs btn-outline">Read More</div>
</section>

<section class="features">
  <h2 class="abs center features-title">Lorem Ipsum Dolor Sit Amet</h2>
  <div class="abs feature" style="left:110px">
    <svg width="30" height="30" viewBox="0 0 30 30"><line x1="5" y1="25" x2="20" y2="10" stroke="#fff" stroke-width="4"/><path d="M22 3l1.5 3.5L27 8l-3.5 1.5L22 13l-1.5-3.5L17 8l3.5-1.5z" fill="#fff"/></svg>
    <h3>Why do you choose Lunacrest ?</h3>
    <p>Morbi scelerisque diam turpis nec rhoncus. Maecenas lobortis, diam sed porta interdum nullam.</p>
  </div>
  <div class="abs feature" style="left:368px">
    <svg width="30" height="30" viewBox="0 0 30 30"><path d="M15 27L4 15a6.5 6.5 0 0 1 11-7 6.5 6.5 0 0 1 11 7z" fill="#fff"/></svg>
    <h3>Why you will Love it?</h3>
    <p>Class aptent taciti sociosqu ad litora torquent per conubia nostra, per inceptos himenaeos volutpat.</p>
  </div>
  <div class="abs feature" style="left:624px">
    <svg width="30" height="30" viewBox="0 0 30 30"><path d="M26 4c-8 0-13 5-16 11l5 5c6-3 11-8 11-16z" fill="#fff"/><path d="M9 16l-5 1 3-5h5zM14 21l-1 5 5-3v-5z" fill="#fff"/></svg>
    <h3>We are Passionate</h3>
    <p>Phasellus sed faucibus magna. Donec at pretium purus. Donec sed magna iaculis in felis cras amet.</p>
  </div>
  <div class="abs feature" style="left:879px">
    <svg width="30" height="30" viewBox="0 0 30 30"><path d="M4 12h5l12-7v20l-12-7H4z" fill="#fff"/><rect x="8" y="18" width="4" height="8" fill="#fff"/></svg>
    <h3>24/7 awesome support</h3>
    <p>Curabitur lacinia vehicula sed eget tristique. Semper neque est, eget vestibulum et luctus amet.</p>
  </div>
</section>

<section class="gallery">
  <h2 class="abs center sec-title">Our Gallery</h2>
  <p class="abs center sec-sub">LOREM IPSUM DOLOR SIT AMET CONSECTETUER DIPICSING</p>
  <div class="abs grid">
    <div class="tile t1" role="img" aria-label="Woman wearing a diamond necklace"></div>
    <div class="tile t2" role="img" aria-label="Diamond chandelier earrings on red"></div>
    <div class="tile t3" role="img" aria-label="Woman with drop earrings"></div>
    <div class="tile t4" role="img" aria-label="Woman wearing stud earrings"></div>
    <div class="tile t5" role="img" aria-label="Smiling woman with pendant"></div>
    <div class="tile t6" role="img" aria-label="Pearl bracelet with ruby ring"></div>
    <div class="tile t7" role="img" aria-label="Diamond tiara"></div>
    <div class="tile t8" role="img" aria-label="Hands showing an engagement ring"></div>
    <div class="tile t9" role="img" aria-label="Heart pendant necklace"></div>
    <div class="tile t10" role="img" aria-label="Wedding band on a hand"></div>
    <div class="tile t11" role="img" aria-label="Manicured hand with diamond ring"></div>
    <div class="tile t12" role="img" aria-label="Woman with dark hair and earrings"></div>
  </div>
</section>

<section class="testimonials">
  <h2 class="abs center sec-title">Testimonials</h2>
  <p class="abs center sec-sub">LOREM IPSUM DOLOR SIT AMET CONSECTETUER DIPICSING</p>
  <div class="abs avatar" style="left:110px" role="img" aria-label="Customer portrait"></div>
  <blockquote class="abs quote" style="left:274px">Sed ut perspiciatis unde omnis iste natus error de sa<cite>- Ellis Marlow</cite></blockquote>
  <div class="abs avatar" style="left:611px" role="img" aria-label="Customer portrait"></div>
  <blockquote class="abs quote" style="left:775px">totam rem aperiam, eaque ipsa quae ab illo inventore<cite>- Noa Brennan</cite></blockquote>
</section>

<section class="types">
  <h2 class="abs center sec-title">Diamond Types</h2>
  <p class="abs center sec-sub">LOREM IPSUM DOLOR SIT AMET CONSECTETUER DIPICSING</p>
  <div class="abs gem" style="left:98px;top:229px"><div class="stone yellow" role="img" aria-label="Yellow cushion-cut diamond"></div>Aldane Diamond</div>
  <div class="abs gem" style="left:388px;top:229px"><div class="stone white" role="img" aria-label="White cushion-cut diamond"></div>Gravelle Diamond</div>
  <div class="abs gem" style="left:646px;top:229px"><div class="stone black" role="img" aria-label="Black cushion-cut diamond"></div>Ambrell Diamond</div>
  <div class="abs gem" style="left:911px;top:229px"><div class="stone green" role="img" aria-label="Green cushion-cut diamond"></div>Zelmara Diamond</div>
  <div class="abs gem" style="left:98px;top:481px"><div class="stone black" role="img" aria-label="Black cushion-cut diamond"></div>Aldane Diamond</div>
  <div class="abs gem" style="left:388px;top:481px"><div class="stone green" role="img" aria-label="Green cushion-cut diamond"></div>Gravelle Diamond</div>
  <div class="abs gem" style="left:646px;top:481px"><div class="stone yellow" role="img" aria-label="Yellow cushion-cut diamond"></div>Ambrell Diamond</div>
  <div class="abs gem" style="left:911px;top:481px"><div class="stone white" role="img" aria-label="White cushion-cut diamond"></div>Zelmara Diamond</div>
</section>

<section class="contact">
  <h2 class="abs center sec-title">Contact Us</h2>
  <p class="abs center sec-sub">LOREM IPSUM DOLOR SIT AMET CONSECTETUER DIPICSING</p>
  <div class="abs field" style="top:196px">Name</div>
  <div class="abs field" style="top:259px">Email</div>
  <div class="abs field" style="top:322px">Phone</div>
  <div class="abs field msg" style="top:196px">Message</div>
  <div class="abs btn-dark">Submit</div>
</section>

<section class="map" role="img" aria-label="Map of Australia showing the business location"></section>
<div class="abs to-top"><svg width="40" height="40" viewBox="0 0 40 40"><path d="M13 22l7-7 7 7M13 28l7-7 7 7" fill="none" stroke="#fff" stroke-width="2.5"/></svg></div>

<footer class="footer">© Copyright 2010-2012 Lunacrest Gems Pty Ltd</footer>

</body>
</html>
```